We need a wordpress design that will incorporate a professional color scheme with company logo in a clean layout. The design needs to consider that this will be developed on a responsive theme. Colors are blue and green of the logo and and an accent color (perhaps very light brown/tan). Client wants a 'modern' look.

Industry/Entity Type

It Company

Font styles to use
Serif
Sans Serif

Colors

Designer to choose colors to be used in the design.

Requirements
Must have
• navigation: 1) Home; 2) Services; 3) Auctions by Type; 4) About Us; 5) QVT Bulletin 6) Videos; 7) Contact Us

VERY general idea of layout is attached, Site will have slideshow, image is attached. Widgets used to are: 1) Email Contact Form; 2) social media icons, QT Linkora, ViewNest; 3) Featured Auctions; 4) News & Events blog; Featured Video

Footer will have affiliation logos, contact info and perhaps smaller company logo:
Phone: (512) 555-0147 / Mobile: (512) 555-0183 (Miriam)
Email: mdorrance482@mailbox-example.com / holden@parkelldorrance.example
Address: 417 FM 1382N • #B208 • PMB315 • Austin, TX 78791

Nice to have
• Use of a dropdown menu

```html
<!DOCTYPE html>
<html lang="en">
<head>
<meta charset="utf-8">
<title>Parkell Dorrance Auction Marketing</title>
<link href="https://fonts.googleapis.com/css2?family=PT+Sans:wght@400;700&family=Roboto+Condensed:wght@400;700&display=swap" rel="stylesheet">
<style>
:root{
  --page-blue:#0f5a8e;
  --brand-blue:#1c4f97;
  --green:#1a8c5b;
  --green-dark:#127046;
  --green-light:#22a06a;
  --panel:#f0f0f0;
  --panel-border:#c9c9c9;
  --dark:#333333;
  --text:#333333;
  --link:#2a6fa8;
  --white:#ffffff;
}
*{box-sizing:border-box;margin:0;padding:0}
html,body{width:834px;height:1200px;overflow:hidden}
body{background:var(--page-blue);font-family:"PT Sans",Arial,sans-serif;color:var(--text);position:relative}
.page{position:absolute;left:96px;top:21px;width:642px;height:1179px;background:var(--white)}
.main-nav{position:absolute;left:0;top:0;width:642px;height:31px;background:linear-gradient(var(--green-light),var(--green));border-radius:4px 4px 0 0;display:flex}
.main-nav a{font-family:"Roboto Condensed",Arial,sans-serif;font-size:10.5px;color:var(--white);text-decoration:none;display:flex;align-items:center;justify-content:center;border-right:1px solid rgba(255,255,255,.25);height:31px}
.main-nav a:last-child{border-right:none}
.dropdown{position:absolute;left:143px;top:31px;width:127px;background:rgba(26,140,91,.93);z-index:3}
.dropdown a{display:block;height:21.5px;line-height:21.5px;padding-left:21px;font-size:9px;font-weight:700;color:var(--white);text-decoration:none;font-family:Arial,sans-serif}
.dropdown a.active{background:var(--brand-blue)}
.hero{position:absolute;left:0;top:31px;width:642px;height:225px;overflow:hidden}
.hero-photo{position:absolute;inset:0;background:linear-gradient(90deg,#ffffff 0%,#ffffff 30%,rgba(255,255,255,0) 48%),linear-gradient(180deg,#8fb4cf 0%,#b9773a 30%,#c88a3e 60%,#7a4a22 100%)}
.brand{position:absolute;left:30px;top:48px;width:180px}
.brand-mark{font-size:26px;font-weight:700;color:var(--brand-blue);display:flex;align-items:center;gap:6px;line-height:1}
.brand-mark i{width:14px;height:14px;background:var(--green);border-radius:50%;display:inline-block}
.brand-name{margin-top:22px;font-size:17.5px;font-weight:700;color:var(--brand-blue);line-height:1.05;text-align:center}
.contact-line{position:absolute;left:28px;font-size:7.5px;font-weight:700;color:#222;display:flex;align-items:center;gap:8px}
.social{position:absolute;right:16px;top:12px;display:flex;gap:6px}
.social span{display:flex;align-items:center;gap:3px;font-size:8px;font-weight:700;color:var(--white);background:rgba(28,79,151,.85);padding:3px 6px 3px 3px;border-radius:11px}
.social span i{width:12px;height:12px;border-radius:50%;background:var(--white);display:inline-block}
.tagline{position:absolute;left:272px;top:185px;width:370px;height:60px;background:rgba(30,30,30,.72);color:var(--white)}
.tagline h2{font-weight:400;font-size:17.5px;padding:14px 0 0 3px}
.tagline a{position:absolute;right:36px;bottom:12px;font-size:8px;color:var(--white);text-decoration:none}
.welcome{position:absolute;left:10px;top:277px;width:395px}
.welcome h1{font-size:16px;font-weight:400;color:#222}
.welcome p{font-size:8.3px;line-height:1.55;margin-top:6px;padding-left:3px}
.auction-card{position:absolute;left:11px;width:394px;height:199px;background:var(--panel);border:1px solid var(--panel-border);border-radius:3px 3px 0 0}
.auction-card header{height:29px;background:linear-gradient(var(--green-light),var(--green));border-radius:3px 3px 0 0;color:var(--white);font-size:11px;line-height:29px;padding-left:14px;font-family:Arial,sans-serif}
.lot-photo{position:absolute;left:22px;top:38px;width:104px;height:68px;background:linear-gradient(180deg,#b7c8d8 0%,#c6d2dc 35%,#8aa060 40%,#5e8040 100%);box-shadow:2px 2px 3px rgba(0,0,0,.35)}
.btn{position:absolute;left:46px;width:67px;height:22px;background:var(--dark);border-radius:4px;color:var(--white);font-size:7.5px;display:flex;align-items:center;gap:8px;padding-left:8px;font-family:Arial,sans-serif}
.btn i{width:11px;height:10px;background:#8fb7e0;border-radius:2px;display:inline-block}
.lot-info{position:absolute;left:143px;top:47px;width:240px;font-family:Arial,sans-serif;letter-spacing:.4px}
.lot-info h3{font-size:10px;font-weight:700;color:#222}
.lot-info .desc{font-size:7.3px;line-height:1.55;margin-top:7px}
.lot-info .bill{display:block;text-align:center;color:var(--link);font-size:8.8px;font-weight:700;margin:9px 0 12px;text-decoration:none;padding-left:60px}
.lot-info .row{font-size:7.3px;line-height:1.7;display:flex;align-items:center;gap:4px}
.lot-info .b{font-weight:700}
.lot-info .date{padding-left:42px}
.pin{width:7px;height:9px}
.sidebar-box{position:absolute;left:434px;background:var(--panel);border:1px solid var(--panel-border);border-radius:4px}
.signup{left:434px;top:273px;width:198px;height:98px;background:#3a3a3a;border:none;color:var(--white);padding:8px 12px}
.signup h2{font-size:16px;font-weight:400}
.signup p{font-size:7.5px;line-height:1.55;margin-top:5px;width:150px}
.signup-form{display:flex;margin-top:8px}
.signup-form .field{width:120px;height:23px;background:var(--green);color:var(--white);font-size:7.5px;line-height:23px;padding-left:7px;font-family:Arial,sans-serif}
.signup-form .submit{width:56px;height:23px;background:#f4f4f4;color:#333;font-size:10px;font-weight:700;text-align:center;line-height:23px;border:1px solid #ccc}
.featured{left:433px;top:406px;width:200px;height:223px;text-align:center;font-family:Arial,sans-serif}
.featured h2{font-family:"PT Sans",Arial,sans-serif;font-size:16px;font-weight:400;text-align:left;padding:14px 0 0 15px}
.featured .title{font-size:7.2px;line-height:1.75;margin-top:10px}
.featured .thumb{width:115px;height:70px;margin:8px auto 0;border:2px solid var(--green);background:linear-gradient(180deg,#d8e2ea 0%,#c0c6ca 40%,#7f8a6a 70%,#56703e 100%)}
.featured .addr{font-size:7.2px;line-height:1.4;margin-top:14px;padding:0 20px}
.video{position:absolute;left:433px;top:665px;width:200px;height:135px;border:1px solid #999;background:linear-gradient(180deg,#e6edf3 0%,#b6bcc0 45%,#8e9c80 80%,#5f7a45 100%)}
.video .play{position:absolute;left:86px;top:34px;width:38px;height:38px;border-radius:50%;background:rgba(0,0,0,.75)}
.video .bar{position:absolute;left:0;bottom:0;width:100%;height:14px;background:#1a1a1a}
.news{left:432px;top:837px;width:200px;height:156px;padding:10px 13px;font-family:Arial,sans-serif}
.news h2{font-family:"PT Sans",Arial,sans-serif;font-size:16px;font-weight:400}
.news ul{list-style:none;margin-top:9px}
.news li{font-size:7.2px;line-height:1.35;margin-bottom:8px;color:#333}
.site-footer{position:absolute;left:0;top:1061px;width:642px;height:118px;background:var(--green);color:var(--white)}
.footer-info{position:absolute;left:15px;top:26px;font-size:7.6px;line-height:1.85;letter-spacing:.3px;font-family:Arial,sans-serif}
.footer-brand{position:absolute;left:390px;top:30px;width:110px;text-align:center;font-weight:700}
.footer-brand .mark{font-size:13px;display:flex;align-items:center;justify-content:center;gap:4px}
.footer-brand .mark i{width:8px;height:8px;border-radius:50%;background:var(--white);display:inline-block}
.footer-brand .name{font-size:10px;line-height:1.15;margin-top:10px}
.badges{position:absolute;left:520px;top:16px;width:110px;height:90px}
.badge{position:absolute;background:rgba(255,255,255,.85)}
</style>
</head>
<body>
<div class="page">
  <nav class="main-nav">
    <a style="width:66px">HOME</a>
    <a style="width:79px">SERVICES</a>
    <a style="width:122px">AUCTIONS BY TYPE</a>
    <a style="width:90px">ABOUT US</a>
    <a style="width:106px">QVT BULLETIN</a>
    <a style="width:69px">VIDEOS</a>
    <a style="width:110px">CONTACT US</a>
  </nav>

  <section class="hero">
    <div class="hero-photo" role="img" aria-label="Photo of a large two-storey home with warm lit windows at dusk"></div>
    <div class="brand">
      <div class="brand-mark"><i></i>Heartland Range</div>
      <div class="brand-name">Parkell Dorrance<br>Auction Marketing</div>
    </div>
    <div class="contact-line" style="top:178px">
      <svg width="14" height="14" viewBox="0 0 14 14"><circle cx="7" cy="7" r="6" fill="none" stroke="#1a8c5b" stroke-width="1.5"/><path d="M5 4l1.3 1.6-.7.9c.4.9 1 1.5 1.9 1.9l.9-.7L10 9l-.9 1.1C6.8 9.8 4.3 7.3 3.9 5z" fill="#1a8c5b"/></svg>
      (512) 555-0147, (512) 555-0183
    </div>
    <div class="contact-line" style="top:199px">
      <svg width="16" height="10" viewBox="0 0 16 10"><rect x="2" y="0.5" width="13" height="9" fill="#1a8c5b"/><path d="M2 .5l6.5 5 6.5-5" fill="none" stroke="#fff" stroke-width="1"/></svg>
      mdorrance482@mailbox-example.com
    </div>
    <div class="social">
      <span><i></i>QT</span>
      <span><i></i>ViewNest</span>
      <span><i></i>Linkora</span>
    </div>
    <div class="tagline">
      <h2>Making "SOLD" Our Specialty for 30 Years</h2>
      <a>Learn More &gt;&gt;</a>
    </div>
  </section>

  <div class="dropdown">
    <a>Real Estate</a>
    <a class="active">Business Liquidations</a>
    <a>Commercial</a>
    <a>Appraisal</a>
  </div>

  <section class="welcome">
    <h1>Welcome To Parkell Dorrance Auction Marketing</h1>
    <p>Our auction business was started in 1977. We conduct farm equipment, logging &amp; industrial equipment, real estate, antique &amp; cattle sales. Parkell Dorrance Auction Marketing, was raised on the family farm in Ashford County.</p>
  </section>

  <article class="auction-card" style="top:365px">
    <header>ONLINE ONLY HALVERN AUCTION - REAL ESTATE</header>
    <div class="lot-photo" role="img" aria-label="Photo of open grassland tract"></div>
    <div class="btn" style="top:120px"><i></i>Details</div>
    <div class="btn" style="top:149px"><i></i>Photos</div>
    <div class="lot-info">
      <h3>THURSDAY, AUGUST 21ST AT 10:00 A.M.</h3>
      <p class="desc">Selling 3120 Acres of land in tracts of 2590 Acres &amp; 560 Acres</p>
      <a class="bill">Click here to view Sale Bill!</a>
      <div class="row b">LIVE OFF-SITE AUCTION</div>
      <div class="row b">Auction Location:</div>
      <div class="row"><svg class="pin" viewBox="0 0 7 9"><path d="M3.5 9L.6 4.5A3 3 0 116.4 4.5z" fill="#d41f1f"/></svg>318 N Elm Ave, Corbin, OK 73851</div>
      <div class="row b">Property Location:</div>
      <div class="row"><svg class="pin" viewBox="0 0 7 9"><path d="M3.5 9L.6 4.5A3 3 0 116.4 4.5z" fill="#d41f1f"/></svg>318 N Elm Ave, Corbin, OK 73851</div>
      <div class="row date">08/21/14 at 10:00 AM CDT</div>
    </div>
  </article>

  <article class="auction-card" style="top:596px">
    <header>ONLINE ONLY HALVERN AUCTION - REAL ESTATE</header>
    <div class="lot-photo" role="img" aria-label="Photo of open grassland tract"></div>
    <div class="btn" style="top:120px"><i></i>Details</div>
    <div class="btn" style="top:149px"><i></i>Photos</div>
    <div class="lot-info">
      <h3>THURSDAY, AUGUST 21ST AT 10:00 A.M.</h3>
      <p class="desc">Selling 3120 Acres of land in tracts of 2590 Acres &amp; 560 Acres</p>
      <a class="bill">Click here to view Sale Bill!</a>
      <div class="row b">LIVE OFF-SITE AUCTION</div>
      <div class="row b">Auction Location:</div>
      <div class="row"><svg class="pin" viewBox="0 0 7 9"><path d="M3.5 9L.6 4.5A3 3 0 116.4 4.5z" fill="#d41f1f"/></svg>318 N Elm Ave, Corbin, OK 73851</div>
      <div class="row b">Property Location:</div>
      <div class="row"><svg class="pin" viewBox="0 0 7 9"><path d="M3.5 9L.6 4.5A3 3 0 116.4 4.5z" fill="#d41f1f"/></svg>318 N Elm Ave, Corbin, OK 73851</div>
      <div class="row date">08/21/14 at 10:00 AM CDT</div>
    </div>
  </article>

  <article class="auction-card" style="top:827px">
    <header>ONLINE ONLY HALVERN AUCTION - REAL ESTATE</header>
    <div class="lot-photo" role="img" aria-label="Photo of open grassland tract"></div>
    <div class="btn" style="top:120px"><i></i>Details</div>
    <div class="btn" style="top:149px"><i></i>Photos</div>
    <div class="lot-info">
      <h3>THURSDAY, AUGUST 21ST AT 10:00 A.M.</h3>
      <p class="desc">Selling 3120 Acres of land in tracts of 2590 Acres &amp; 560 Acres</p>
      <a class="bill">Click here to view Sale Bill!</a>
      <div class="row b">LIVE OFF-SITE AUCTION</div>
      <div class="row b">Auction Location:</div>
      <div class="row"><svg class="pin" viewBox="0 0 7 9"><path d="M3.5 9L.6 4.5A3 3 0 116.4 4.5z" fill="#d41f1f"/></svg>318 N Elm Ave, Corbin, OK 73851</div>
      <div class="row b">Property Location:</div>
      <div class="row"><svg class="pin" viewBox="0 0 7 9"><path d="M3.5 9L.6 4.5A3 3 0 116.4 4.5z" fill="#d41f1f"/></svg>318 N Elm Ave, Corbin, OK 73851</div>
      <div class="row date">08/21/14 at 10:00 AM CDT</div>
    </div>
  </article>

  <aside class="sidebar-box signup">
    <h2>Email Signup</h2>
    <p>Please join our free mailing list to get auction alerts.</p>
    <div class="signup-form">
      <div class="field">Enter Your Email</div>
      <div class="submit">Submit</div>
    </div>
  </aside>

  <aside class="sidebar-box featured">
    <h2>Featured Auction</h2>
    <p class="title">13.35 ACRES OF PRIME DEVELOP<br>&amp; 33RD STREET</p>
    <div class="thumb" role="img" aria-label="Photo of a house with a crowd gathered for an auction"></div>
    <p class="addr">LOTS 13 &amp; 14 FOR SALE, BRAMWELL IOWA<br>Third Street, Bramwell, IA 52690</p>
  </aside>

  <div class="video" role="img" aria-label="Featured video still of a house with a wraparound porch">
    <div class="play"><svg width="38" height="38" viewBox="0 0 38 38"><path d="M15 11l12 8-12 8z" fill="#fff"/></svg></div>
    <div class="bar"><svg width="200" height="14" viewBox="0 0 200 14"><path d="M6 4l5 3-5 3z" fill="#fff"/><rect x="18" y="6" width="96" height="2" fill="#666"/><rect x="18" y="5" width="4" height="4" fill="#fff"/><text x="128" y="10" fill="#aaa" font-size="6" font-family="Arial">00:00 / 04:36</text></svg></div>
  </div>

  <aside class="sidebar-box news">
    <h2>News Events</h2>
    <ul>
      <li>Great Land Auction Companies Make All the Difference</li>
      <li>Great OK Farms for Sale at Auction Prices</li>
      <li>Farmland Auctions on Route 66</li>
      <li>Great Land Auction Companies Make All the Difference</li>
      <li>Great OK Farms for Sale at Auction Prices</li>
    </ul>
  </aside>

  <footer class="site-footer">
    <div class="footer-info">
      Phone: (512) 555-0147 / Mobile: (512) 555-0183 (Miriam)<br>
      Email: mdorrance482@mailbox-example.com / holden@parkelldorrance.example<br>
      Address: 417 FM 1382N • #B208 • PMB315 • Austin, TX 78791<br>
      Copyright © 2005 - 2014: Parkell Dorrance Auction Marketing, Inc.<br>
      All Rights Reserved • Powered by: AuctionDeskPro.example and LotRegistry.example
    </div>
    <div class="footer-brand">
      <div class="mark"><i></i>Heartland Range</div>
      <div class="name">Parkell Dorrance<br>Auction Marketing</div>
    </div>
    <div class="badges" role="img" aria-label="Affiliation badges">
      <div class="badge" style="left:10px;top:0;width:34px;height:34px;border-radius:50%"></div>
      <div class="badge" style="left:62px;top:0;width:30px;height:34px"></div>
      <div class="badge" style="left:8px;top:42px;width:36px;height:34px;border-radius:4px"></div>
      <div class="badge" style="left:50px;top:46px;width:60px;height:26px"></div>
    </div>
  </footer>
</div>
</body>
</html>
```